Brookvane Consulting Business Card Design

Business Card Design for Brookvane Consulting. Brookvane Consulting is a boutique consultancy based in Atlanta, GA., that specializes in marketing strategy, organization planning, and leadership development. We provide solutions for small businesses and startups as well as Vantage 300 companies.

http://brookvaneconsulting.com/

Target Market(s)

We provide solutions for small businesses and startups as well as Vantage 300 companies.

Industry/Entity Type

Consulting

Contact Information for Business Card

Two sided business card with priority on contact information, logo, tag line (Guidance to Plan Boldly, Act Wisely, Grow Steadily)

Colors

Designer to choose colors to be used in the design.

Requirements
Must have
• contact information, logo, tag line (Guidance to Plan Boldly, Act Wisely, Grow Steadily)
• Simple no over communication.
Nice to have
• I would like to see different placements of logo and creative use of both sides of the card
Should not have
• Do not put too much information on the card.

```html
<!DOCTYPE html>
<html lang="en">
<head>
<meta charset="utf-8">
<title>Brookvane Consulting Business Card</title>
<link href="https://fonts.googleapis.com/css2?family=Montserrat:wght@300;400&family=Pacifico&display=swap" rel="stylesheet">
<style>
  :root {
    --backdrop: #1f1f1f;
    --card: #333333;
    --ink: #ffffff;
    --ink-soft: #e6e6e6;
  }
  * { box-sizing: border-box; margin: 0; padding: 0; }
  html, body {
    width: 799px;
    height: 1200px;
    overflow: hidden;
    background: var(--backdrop);
  }
  .sheet {
    position: relative;
    width: 799px;
    height: 1200px;
  }
  .card {
    position: absolute;
    left: 80px;
    width: 640px;
    height: 366px;
    background: var(--card);
    border-radius: 26px;
    color: var(--ink);
    font-family: "Montserrat", sans-serif;
    box-shadow: 0 18px 40px rgba(0,0,0,0.45);
  }
  .card--front { top: 130px; }
  .card--back { top: 700px; }

  .wordmark {
    font-family: "Montserrat", sans-serif;
    font-weight: 300;
    color: var(--ink);
    letter-spacing: 0.06em;
    text-transform: uppercase;
    line-height: 1.1;
  }
  .wordmark span { display: block; }
  .card--front .wordmark {
    position: absolute;
    left: 0; right: 0;
    top: 120px;
    text-align: center;
    font-size: 50px;
  }
  .card--front .wordmark span { font-size: 30px; letter-spacing: 0.32em; margin-top: 10px; }

  .holder-name {
    position: absolute;
    left: 50px;
    top: 44px;
    font-family: "Pacifico", cursive;
    font-size: 20px;
    color: var(--ink);
  }
  .contact {
    position: absolute;
    left: 50px;
    bottom: 52px;
    list-style: none;
    font-size: 15px;
    line-height: 1.35;
    color: var(--ink-soft);
  }
  .brand-block {
    position: absolute;
    right: 44px;
    top: 86px;
    width: 260px;
  }
  .brand-block .wordmark { font-size: 27px; }
  .brand-block .wordmark span { font-size: 16px; letter-spacing: 0.3em; margin-top: 4px; }
  .tagline {
    margin-top: 6px;
    font-size: 9.5px;
    font-weight: 400;
    letter-spacing: 0.02em;
    color: var(--ink-soft);
    white-space: nowrap;
  }
</style>
</head>
<body>
  <main class="sheet">
    <section class="card card--front" aria-label="Card front">
      <p class="wordmark">Brookvane<span>Consulting</span></p>
    </section>

    <section class="card card--back" aria-label="Card back">
      <p class="holder-name">Darren</p>
      <div class="brand-block">
        <p class="wordmark">Brookvane<span>Consulting</span></p>
        <p class="tagline">Guidance to Plan Boldly, Act Wisely, Grow Steadily</p>
      </div>
      <ul class="contact">
        <li>555-201-4730</li>
        <li>darren@brookvaneconsulting.com</li>
        <li>www.brookvaneconsulting.com</li>
      </ul>
    </section>
  </main>
</body>
</html>
```